RTavenor Business Cards & Letterhead

I have a logo but need a design for some new business cards. We are a Design-Build Firm that specializes in the design and construction of commercial projects.
the cards need to be professional. no cartoon stuff.
i would like to have the cards in AI format so I can update the card as needed. Logo is provided.
Our Address is: 4187 Marlowe Ct. Corvane, West Haddon 27614

```html
<!DOCTYPE html>
<html lang="en">
<head>
<meta charset="UTF-8">
<title>RTavenor Business Cards</title>
<link href="https://fonts.googleapis.com/css2?family=Open+Sans:wght@400;600;700;800&display=swap" rel="stylesheet">
<style>
  :root {
    --stage: #333333;
    --card-dark: #222227;
    --band-white: #ffffff;
    --brand-blue: #1a78c2;
    --blue-light: #1577b8;
    --blue-deep: #0a3a63;
    --wordmark-back: #0c4a7e;
    --logo-gray: #6d6e71;
    --text-light: #f2f2f2;
    --rule: #d9d9d9;
  }
  * { box-sizing: border-box; margin: 0; padding: 0; }
  html, body {
    width: 1200px; height: 780px; overflow: hidden;
    background: var(--stage);
    font-family: "Open Sans", Arial, sans-serif;
  }
  .sheet {
    width: 1200px; height: 780px;
    display: flex; align-items: center; justify-content: center; gap: 50px;
  }
  .card {
    position: relative;
    width: 525px; height: 300px;
    overflow: hidden;
  }

  /* Back side */
  .card-back {
    background: radial-gradient(ellipse at 50% 55%, var(--blue-light) 0%, #10598f 45%, var(--blue-deep) 100%);
    display: flex; align-items: center; justify-content: center;
  }
  .back-wordmark {
    font-weight: 800;
    font-size: 62px;
    letter-spacing: 2px;
    color: var(--wordmark-back);
    text-transform: uppercase;
  }

  /* Front side */
  .card-front { background: var(--card-dark); }
  .logo-band {
    position: absolute; left: 0; top: 0;
    width: 92px; height: 100%;
    background: var(--band-white);
  }
  .band-wordmark {
    position: absolute;
    left: 46px; top: 150px;
    transform: translate(-50%, -50%) rotate(-90deg);
    font-weight: 800;
    font-size: 28px;
    letter-spacing: 1px;
    color: var(--logo-gray);
    white-space: nowrap;
    text-transform: uppercase;
  }
  .name-block {
    position: absolute; right: 34px; top: 26px;
    text-align: right;
  }
  .person-name {
    font-weight: 700;
    font-size: 23px;
    letter-spacing: 1px;
    color: var(--brand-blue);
    line-height: 1.1;
  }
  .person-title {
    font-weight: 600;
    font-size: 14px;
    letter-spacing: 0.5px;
    color: var(--text-light);
    margin-top: 2px;
  }
  .name-accent {
    position: absolute; right: 14px; top: 22px;
    width: 14px; height: 52px;
    background: linear-gradient(90deg, #0f4f86, var(--brand-blue));
  }
  .divider {
    position: absolute; left: 92px; right: 12px; top: 86px;
    height: 1px; background: var(--rule);
  }
  .contact {
    position: absolute; right: 40px; bottom: 36px;
    text-align: right;
    color: var(--text-light);
    font-size: 13.5px;
    line-height: 1.35;
    letter-spacing: 0.3px;
  }
  .contact .address { margin-bottom: 8px; }
  .contact-icons {
    position: absolute; right: 16px; bottom: 40px;
    display: flex; flex-direction: column; gap: 5px;
  }
  .contact-icons svg { width: 13px; height: 13px; display: block; }
</style>
</head>
<body>
<main class="sheet">
  <section class="card card-back" aria-label="Business card back">
    <span class="back-wordmark">RTavenor</span>
  </section>

  <section class="card card-front" aria-label="Business card front">
    <div class="logo-band">
      <span class="band-wordmark">RTavenor</span>
    </div>

    <div class="name-accent"></div>
    <div class="name-block">
      <p class="person-name">MARCUS TAVENOR</p>
      <p class="person-title">Founder/President</p>
    </div>
    <div class="divider"></div>

    <div class="contact">
      <p class="address">4187 Marlowe Ct. Corvane,<br>West Haddon 27614</p>
      <p>(555) 384-0148</p>
      <p>www.rtavenor.com</p>
      <p>MRT@RTavenor.com</p>
    </div>

    <div class="contact-icons">
      <svg viewBox="0 0 16 16" aria-label="Phone" role="img">
        <path d="M3 1.5h3l1.2 3.3-1.8 1.3a8 8 0 0 0 4.5 4.5l1.3-1.8 3.3 1.2v3a1.5 1.5 0 0 1-1.6 1.5A13 13 0 0 1 1.5 3.1 1.5 1.5 0 0 1 3 1.5z" fill="var(--brand-blue)"/>
      </svg>
      <svg viewBox="0 0 16 16" aria-label="Website" role="img">
        <circle cx="8" cy="8" r="6.5" fill="none" stroke="var(--brand-blue)" stroke-width="1.6"/>
        <ellipse cx="8" cy="8" rx="2.8" ry="6.5" fill="none" stroke="var(--brand-blue)" stroke-width="1.2"/>
        <line x1="1.5" y1="8" x2="14.5" y2="8" stroke="var(--brand-blue)" stroke-width="1.2"/>
      </svg>
      <svg viewBox="0 0 16 16" aria-label="Email" role="img">
        <rect x="1" y="3" width="14" height="10" rx="1" fill="var(--brand-blue)"/>
        <path d="M1.5 3.8 8 9l6.5-5.2" fill="none" stroke="var(--card-dark)" stroke-width="1.3"/>
      </svg>
    </div>
  </section>
</main>
</body>
</html>
```